Calvanto Group Real Estate Company business cards

New business card design, we are generally happy with the basic layout of the existing front of business card, (feel free to change) but require a head shot photo on the back side.

http://www.calvanto.com.au/

Attached logos, and existing business card

------------------------------

Target Market(s)

Real estate

Industry/Entity Type

Real Estate

Contact Information for Business Card

Standard size double sided

Font styles to use
Other font styles liked:
• Futura

Requirements
Must have
• Photo head shot on the back side
Nice to have
• yes
Should not have
• No

```html
<!DOCTYPE html>
<html lang="en">
<head>
<meta charset="utf-8">
<title>Calvanto Group Business Cards</title>
<link rel="stylesheet" href="https://fonts.googleapis.com/css2?family=Jost:wght@400;500&family=Roboto+Condensed:wght@700&family=Roboto:wght@400&display=swap">
<style>
  :root {
    --bg: #d9d9db;
    --card: #f7f7f8;
    --purple: #2b1a4d;
    --orange: #ee7a12;
    --ink: #2e2c3a;
    --photo-a: #e9ebef;
    --photo-b: #3b4766;
  }
  * { margin: 0; padding: 0; box-sizing: border-box; }
  html, body { width: 1200px; height: 1200px; overflow: hidden; }
  body {
    background: var(--bg);
    display: flex;
    flex-direction: column;
    align-items: center;
    justify-content: center;
    gap: 60px;
  }
  .card {
    position: relative;
    width: 840px;
    height: 480px;
    background: var(--card);
    border-radius: 26px;
    overflow: hidden;
    box-shadow: 0 2px 6px rgba(0,0,0,0.12);
  }

  /* Front */
  .headline {
    position: absolute;
    left: 70px;
    top: 150px;
    font-family: "Jost", sans-serif;
    font-weight: 400;
    font-size: 44px;
    line-height: 1.05;
    color: var(--purple);
  }
  .headline .accent { color: var(--orange); }
  .wordmark {
    font-family: "Jost", sans-serif;
    font-weight: 500;
    color: var(--purple);
    letter-spacing: 0.5px;
    white-space: nowrap;
  }
  .front .wordmark {
    position: absolute;
    left: 70px;
    top: 340px;
    font-size: 58px;
  }
  .headshot {
    position: absolute;
    right: 0;
    top: 0;
    width: 330px;
    height: 420px;
    background: linear-gradient(180deg, var(--photo-a) 0%, var(--photo-a) 35%, var(--photo-b) 100%);
  }

  /* Back */
  .back .wordmark {
    position: absolute;
    right: 60px;
    top: 56px;
    font-size: 56px;
  }
  .contacts {
    position: absolute;
    left: 520px;
    top: 168px;
    list-style: none;
    font-family: "Roboto", sans-serif;
    font-size: 19px;
    color: var(--ink);
  }
  .contacts li {
    display: flex;
    align-items: center;
    gap: 14px;
    height: 30px;
  }
  .contacts svg { width: 18px; height: 18px; flex: none; }
  .person {
    position: absolute;
    left: 70px;
    top: 300px;
  }
  .person .name {
    font-family: "Roboto Condensed", sans-serif;
    font-weight: 700;
    font-size: 34px;
    color: var(--purple);
    letter-spacing: 0.5px;
  }
  .person .role {
    font-family: "Roboto", sans-serif;
    font-size: 18px;
    color: var(--ink);
    margin-top: 8px;
  }
  .social {
    position: absolute;
    left: 70px;
    top: 404px;
    display: flex;
    align-items: center;
    gap: 8px;
    font-family: "Roboto", sans-serif;
    font-size: 19px;
    color: var(--ink);
  }
  .social .label { margin-right: 6px; }
  .social .dot {
    width: 26px;
    height: 26px;
    border-radius: 5px;
    background: var(--orange);
  }
  .bands {
    position: absolute;
    left: 0;
    top: 0;
    width: 840px;
    height: 480px;
  }
  .abn {
    position: absolute;
    left: 575px;
    top: 410px;
    font-family: "Roboto", sans-serif;
    font-size: 19px;
    color: #ffffff;
    letter-spacing: 0.5px;
  }
</style>
</head>
<body>

  <section class="card front">
    <p class="headline">Let us<br>show you<br><span class="accent">property</span></p>
    <div class="wordmark">Calvanto Group</div>
    <div class="headshot" role="img" aria-label="Head-and-shoulders portrait of the director in a navy suit and blue tie"></div>
  </section>

  <section class="card back">
    <svg class="bands" viewBox="0 0 840 480" aria-hidden="true">
      <polygon points="0,452 540,452 532,480 0,480" fill="var(--orange)"/>
      <polygon points="520,480 548,385 840,385 840,480" fill="var(--purple)"/>
    </svg>

    <div class="wordmark">Calvanto Group</div>

    <ul class="contacts">
      <li>
        <svg viewBox="0 0 18 18"><rect x="4" y="1" width="10" height="16" rx="2" fill="var(--orange)"/><rect x="6" y="3.5" width="6" height="9" fill="#fff"/></svg>
        0400 555 218
      </li>
      <li>
        <svg viewBox="0 0 18 18"><circle cx="9" cy="9" r="7.5" fill="var(--orange)"/><path d="M1.5 9h15M9 1.5c-3 3.5-3 11.5 0 15M9 1.5c3 3.5 3 11.5 0 15" stroke="#fff" stroke-width="1.2" fill="none"/></svg>
        www.calvanto.com.au
      </li>
      <li>
        <svg viewBox="0 0 18 18"><rect x="1" y="3.5" width="16" height="11" rx="1" fill="var(--orange)"/><path d="M1.5 4.5 9 10l7.5-5.5" stroke="#fff" stroke-width="1.4" fill="none"/></svg>
        daniel.tran@calvanto.com.au
      </li>
    </ul>

    <div class="person">
      <p class="name">DANIEL TRAN</p>
      <p class="role">Director</p>
    </div>

    <div class="social">
      <span class="label">Find us:</span>
      <span class="dot"></span>
      <span class="dot"></span>
      <span class="dot"></span>
    </div>

    <p class="abn">ABN: 12 345 678 901</p>
  </section>

</body>
</html>
```